RTavenor Business Cards & Letterhead

I have a logo but need a design for some new business cards. We are a Design-Build Firm that specializes in the design and construction of commercial projects.
the cards need to be professional. no cartoon stuff.
i would like to have the cards in AI format so I can update the card as needed. Logo is provided.
Our Address is: 4187 Marlowe Ct. Brenford, Vermont 27614

```html
<!DOCTYPE html>
<html lang="en">
<head>
<meta charset="utf-8">
<title>RTavenor Business Card</title>
<link rel="stylesheet" href="https://fonts.googleapis.com/css2?family=Montserrat:wght@400;500;700;800&display=swap">
<style>
  :root {
    --backdrop-top: #cfcfcf;
    --backdrop-bottom: #a9a9a9;
    --card-white: #ffffff;
    --ink-dark: #1f1f1f;
    --ink-soft: #2b2b2b;
    --brand-blue: #1479bd;
    --brand-blue-deep: #0c4f86;
    --card-black: #232323;
  }
  * { margin: 0; padding: 0; box-sizing: border-box; }
  html, body { width: 1200px; height: 815px; overflow: hidden; }
  body {
    background: linear-gradient(180deg, var(--backdrop-top), var(--backdrop-bottom));
    font-family: "Montserrat", Arial, sans-serif;
    position: relative;
  }
  .card {
    position: absolute;
    width: 540px;
    height: 309px;
    border-radius: 16px;
    overflow: hidden;
    box-shadow: 0 14px 30px rgba(0,0,0,0.28);
  }
  /* Front */
  .card-front { left: 40px; top: 253px; background: var(--card-white); }
  .front-brand {
    position: absolute; left: 0; right: 0; top: 56px;
    display: flex; justify-content: center; align-items: center; gap: 12px;
  }
  .brand-square { width: 30px; height: 30px; background: var(--brand-blue); }
  .brand-name {
    font-weight: 800; font-size: 46px; letter-spacing: 1px;
    color: var(--ink-dark); line-height: 1;
  }
  .person { position: absolute; left: 60px; top: 148px; text-align: right; width: 180px; }
  .person-name { color: var(--brand-blue); font-weight: 800; font-size: 20px; letter-spacing: 1px; }
  .person-title { color: var(--ink-soft); font-weight: 500; font-size: 13px; letter-spacing: 2px; margin-top: 2px; }
  .divider { position: absolute; left: 262px; top: 140px; width: 1.5px; height: 62px; background: var(--brand-blue); }
  .contact-list { position: absolute; left: 282px; top: 136px; list-style: none; }
  .contact-list li {
    display: flex; align-items: center; gap: 9px;
    font-size: 13px; color: var(--ink-soft); height: 23px;
  }
  .contact-list svg { width: 12px; height: 12px; fill: var(--brand-blue); flex: none; }
  .front-band { position: absolute; left: 0; top: 0; width: 540px; height: 309px; }
  .address {
    position: absolute; left: 150px; top: 258px; width: 320px;
    text-align: center; color: var(--card-white); font-size: 12px; letter-spacing: 0.3px;
    line-height: 24px; white-space: nowrap;
  }
  /* Back */
  .card-back { left: 620px; top: 253px; background: var(--card-black); }
  .back-panel {
    position: absolute; left: 0; top: 0; width: 210px; height: 309px;
    background: radial-gradient(circle at 70% 40%, #1f8ad0 0%, var(--brand-blue) 40%, var(--brand-blue-deep) 100%);
  }
  .back-brand {
    position: absolute; right: 36px; bottom: 60px;
    display: flex; align-items: center; gap: 10px;
  }
  .back-brand .brand-square { width: 12px; height: 12px; background: var(--card-white); }
  .back-brand .brand-name { color: var(--card-white); font-size: 40px; }
</style>
</head>
<body>

<section class="card card-front">
  <svg class="front-band" viewBox="0 0 540 309" aria-hidden="true">
    <polygon points="0,274 132,274 122,290 0,290" fill="var(--brand-blue)"/>
    <polygon points="150,252 472,252 462,290 138,290" fill="var(--card-black)"/>
    <polygon points="478,252 540,252 540,264 474,264" fill="var(--brand-blue)"/>
  </svg>

  <div class="front-brand">
    <span class="brand-square"></span>
    <span class="brand-name">RTAVENOR</span>
  </div>

  <div class="person">
    <p class="person-name">DORIAN PELL</p>
    <p class="person-title">MANAGER</p>
  </div>

  <span class="divider"></span>

  <ul class="contact-list">
    <li>
      <svg viewBox="0 0 24 24"><path d="M6.6 10.8a15.1 15.1 0 0 0 6.6 6.6l2.2-2.2c.3-.3.7-.4 1-.2 1.1.4 2.3.6 3.6.6.6 0 1 .4 1 1V20c0 .6-.4 1-1 1A17 17 0 0 1 3 4c0-.6.4-1 1-1h3.5c.6 0 1 .4 1 1 0 1.3.2 2.5.6 3.6.1.3 0 .7-.2 1z"/></svg>
      123-456-7890
    </li>
    <li>
      <svg viewBox="0 0 24 24"><path d="M2 5h20v14H2z M2 5l10 8 10-8"/></svg>
      info@youremail.com
    </li>
    <li>
      <svg viewBox="0 0 24 24"><circle cx="12" cy="12" r="10"/></svg>
      www.yourwebsite.com
    </li>
  </ul>

  <p class="address">4187 Marlowe Ct. Brenford, Vermont 27614</p>
</section>

<section class="card card-back">
  <div class="back-panel" role="img" aria-label="Large blue brand decoration"></div>
  <div class="back-brand">
    <span class="brand-square"></span>
    <span class="brand-name">RTAVENOR</span>
  </div>
</section>

</body>
</html>
```